Business Card Design For A Cajun Seafood Restaurant

We are opening a cajun seafood restaurant in a week. We mainly serve cajun seafood which is orginally from Louisiana. We want design on both sides of a business card. I have menu on the website. You can go to www.reednkettle.example to check out our menu.

Restaurant name: Reed N' Kettle
Phone: +1 (555) 304-7712
Address: 48206 Ludlow Row, #7, Bexmoor Flats, Ca90000
Email: reednkettle@mailbox.example
Website: www.reednkettle.example

Maybe add social media icons (facebook, instagram) if looks nice on the business card.
facebook.com/reednkettle
instagram.com/reednkettle or @reednkettle

Attached is the logo and other business card samples that I like.

```html
<!DOCTYPE html>
<html lang="en">
<head>
<meta charset="utf-8">
<title>Reed N' Kettle – Business Card</title>
<link href="https://fonts.googleapis.com/css2?family=Lato:wght@400;700&display=swap" rel="stylesheet">
<style>
  :root{
    --backdrop:#3a3330;
    --card:#222426;
    --brand-yellow:#f2b705;
    --brand-orange:#f26a1b;
    --text-light:#f1f1f1;
    --text-muted:#c9c9c9;
    --rule:#d8d8d8;
  }
  *{box-sizing:border-box;margin:0;padding:0}
  html,body{width:1200px;height:780px;overflow:hidden}
  body{background:var(--backdrop);font-family:'Lato',Arial,sans-serif;position:relative}

  .card{position:absolute;top:235px;width:540px;height:310px;background:var(--card);border-radius:4px;box-shadow:0 10px 30px rgba(0,0,0,.45);overflow:hidden}
  .card--front{left:40px}
  .card--back{left:620px}

  .brand{position:absolute;display:flex;align-items:center;gap:12px}
  .brand__dot{width:18px;height:18px;border-radius:50%;background:var(--brand-orange);flex:none}
  .brand__name{font-weight:700;color:var(--brand-yellow);font-size:30px;letter-spacing:1px;white-space:nowrap;line-height:1}

  .card--front .brand{left:50%;top:50%;transform:translate(-50%,-50%)}
  .card--back .brand{right:48px;top:92px}
  .card--back .brand__name{font-size:26px}

  .contact{position:absolute;left:0;right:0;top:198px;display:flex;justify-content:center;gap:22px}
  .person{text-align:right;padding-top:4px}
  .person__name{color:var(--brand-orange);font-weight:700;font-size:18px;line-height:22px}
  .person__role{color:var(--text-muted);font-size:13px;margin-top:2px}
  .social{display:flex;align-items:center;justify-content:flex-end;gap:8px;margin-top:12px;color:var(--text-light);font-size:13px}
  .social__mark{width:16px;height:16px;border-radius:3px;background:var(--brand-orange)}
  .divider{width:1px;background:var(--rule);height:78px}
  .details{color:var(--text-light);font-size:13px;line-height:19px;padding-top:2px}
  .details__row{display:flex;align-items:center;gap:6px}
  .icon{width:15px;height:15px;border-radius:2px;background:var(--brand-orange);display:inline-flex;align-items:center;justify-content:center;flex:none}
</style>
</head>
<body>
  <section class="card card--front" aria-label="Card front">
    <div class="brand">
      <span class="brand__dot"></span>
      <span class="brand__name">Reed N' Kettle</span>
    </div>
  </section>

  <section class="card card--back" aria-label="Card back">
    <div class="brand">
      <span class="brand__dot"></span>
      <span class="brand__name">Reed N' Kettle</span>
    </div>

    <div class="contact">
      <div class="person">
        <div class="person__name">Dana Whitlow</div>
        <div class="person__role">Managing Director</div>
        <div class="social">
          <span class="social__mark"></span>
          <span>reednkettle</span>
        </div>
      </div>
      <div class="divider"></div>
      <div class="details">
        <div>48206 Ludlow Row, #7</div>
        <div>Bexmoor Flats, Ca90000</div>
        <div class="details__row">
          <span class="icon"><svg width="9" height="9" viewBox="0 0 10 10"><path d="M2 1 L4 1 L5 3.5 L3.8 4.5 Q4.8 6.3 5.5 6.2 L6.5 5 L9 6 L9 8 Q9 9 8 9 Q1 8.5 1 2 Q1 1 2 1Z" fill="#fff"/></svg></span>
          <span>+1 (555) 304-7712</span>
        </div>
        <div class="details__row">
          <span class="icon"><svg width="10" height="8" viewBox="0 0 10 8"><rect x=".5" y=".5" width="9" height="7" fill="none" stroke="#fff"/><path d="M.5 .5 L5 4.5 L9.5 .5" fill="none" stroke="#fff"/></svg></span>
          <span>reednkettle@mailbox.example</span>
        </div>
      </div>
    </div>
  </section>
</body>
</html>
```